Flyers

Modify Existing Flyer and create another for exterior company
Updates

Previous Brief has been updated- we want to update this existing one also

Target Market(s)

Exterior Remodeling Customers

Industry/Entity Type

Remodeling/Construction

```html
<!DOCTYPE html>
<html lang="en">
<head>
<meta charset="utf-8">
<title>Northbrook Roofing and Exteriors – Remodeling Flyer</title>
<link href="https://fonts.googleapis.com/css2?family=Montserrat:wght@500;600;700;800&display=swap" rel="stylesheet">
<style>
  :root{
    --blue:#3b86e6;
    --orange:#f1421b;
    --ink:#1b1b1b;
    --white:#ffffff;
    --soft:#ffe2d9;
  }
  html,body{margin:0;padding:0;overflow:hidden;background:#fff;}
  .flyer{
    position:relative;width:849px;height:1200px;overflow:hidden;
    background:linear-gradient(180deg,#f4f5f6 0%,#e9ebed 60%,#f2f3f4 100%);
    font-family:'Montserrat',sans-serif;color:var(--ink);
  }
  .abs{position:absolute;}
  .shapes{position:absolute;left:0;top:0;}
  /* brand */
  .brand{left:34px;top:94px;display:flex;align-items:center;gap:10px;
    font-weight:800;font-size:17px;line-height:1;color:var(--ink);letter-spacing:.3px;white-space:nowrap;}
  .brand .mark{width:14px;height:14px;background:var(--blue);flex:none;}
  /* headline */
  .headline{left:33px;top:214px;color:var(--white);}
  .headline .lead{font-weight:700;font-size:30px;line-height:30px;}
  .headline .big{font-weight:800;font-size:71px;line-height:74px;letter-spacing:1px;margin-top:8px;}
  .headline .place{font-weight:700;font-size:30px;line-height:30px;margin-top:6px;}
  /* section tabs */
  .tab{font-weight:800;font-size:22px;line-height:1;display:flex;align-items:center;padding-left:33px;box-sizing:border-box;}
  .tab-light{color:var(--ink);}
  .tab-dark{color:var(--white);padding-left:27px;}
  .copy{font-weight:600;font-size:12px;line-height:16px;}
  .copy-light{color:var(--white);}
  .list{margin:0;padding:0;list-style:none;font-weight:500;font-size:12px;line-height:18.5px;white-space:nowrap;}
  .list-soft{color:var(--soft);}
  .list-bullet li::before{content:"";display:inline-block;width:5px;height:5px;border-radius:50%;background:currentColor;margin-right:6px;vertical-align:middle;}
  .list-ink{color:var(--ink);font-size:13px;}
  /* photo slots */
  .photo{position:absolute;}
  .photo-room{left:437px;top:560px;width:166px;height:166px;background:var(--blue);}
  .photo-room .fill{position:absolute;inset:5px;background:linear-gradient(180deg,#c9d3d8 0%,#dfe3e2 55%,#b99a7e 100%);}
  .photo-lounge{left:653px;top:823px;width:196px;height:123px;background:linear-gradient(180deg,#3f5f87 0%,#4b6c95 60%,#d9d6cf 100%);}
  /* call to action */
  .cta{left:581px;top:1135px;width:268px;height:65px;color:var(--white);text-align:right;}
  .cta .ask{position:absolute;right:17px;top:10px;font-weight:700;font-size:9.5px;letter-spacing:.2px;white-space:nowrap;}
  .cta .phone{position:absolute;right:17px;top:23px;font-weight:800;font-size:21px;}
  .cta .web{position:absolute;right:17px;top:49px;font-weight:700;font-size:8.5px;letter-spacing:.4px;}
</style>
</head>
<body>
<div class="flyer">

  <svg class="shapes" width="849" height="1200" viewBox="0 0 849 1200">
    <defs>
      <linearGradient id="kitchenTone" x1="0" y1="0" x2="1" y2="1">
        <stop offset="0" stop-color="#2a2c30"/>
        <stop offset="0.45" stop-color="#1a1c20"/>
        <stop offset="0.75" stop-color="#3a3d44"/>
        <stop offset="1" stop-color="#4a5a3a"/>
      </linearGradient>
    </defs>
    <polygon points="0,194 380,194 441,531 0,531" fill="var(--blue)"/>
    <rect x="0" y="553" width="409" height="624" fill="var(--orange)"/>
    <rect x="0" y="1177" width="409" height="23" fill="var(--blue)"/>
    <rect x="409" y="1177" width="440" height="23" fill="var(--orange)"/>
    <polygon points="0,580 313,580 328,609 0,609" fill="var(--white)"/>
    <polygon points="0,829 354,829 369,860 0,860" fill="var(--white)"/>
    <polygon points="0,1011 354,1011 369,1040 0,1040" fill="var(--white)"/>
    <polygon points="410,740 668,740 684,769 410,769" fill="var(--ink)"/>
    <polygon points="410,965 760,965 776,995 410,995" fill="var(--ink)"/>
    <polygon points="608,1135 849,1135 849,1200 608,1200 581,1168" fill="var(--orange)"/>
    <polyline points="612,1139 588,1168 612,1197" fill="none" stroke="var(--ink)" stroke-width="3"/>
  </svg>

  <svg class="shapes" width="849" height="1200" viewBox="0 0 849 1200" role="img" aria-label="Photo of a dark kitchen sink with a tall faucet, granite countertop and potted plants">
    <polygon points="554,0 849,0 849,794 773,794 383,438 260,328" fill="url(#kitchenTone)"/>
  </svg>

  <div class="abs brand"><span class="mark"></span>NORTHBROOK ROOFING AND EXTERIORS</div>

  <div class="abs headline">
    <div class="lead">Work with a<br>Top-rated<br>Local</div>
    <div class="big">REMODELING<br>COMPANY</div>
    <div class="place">in Ankeny, IA</div>
  </div>

  <!-- kitchen -->
  <div class="abs tab tab-light" style="left:0;top:580px;width:328px;height:29px;">KITCHEN REMODELING</div>
  <div class="abs copy copy-light" style="left:33px;top:618px;width:370px;">Whatever your vision is for your new kitchen,<br>our crew can help you bring it to life. You can trust us for:</div>
  <ul class="abs list list-soft" style="left:33px;top:652px;">
    <li>Open concept design services</li>
    <li>Kitchen cabinet installation services</li>
    <li>Kitchen countertop installation services</li>
    <li>Lighting installation services</li>
    <li>Tile installation services</li>
    <li>Plumbing upgrade services</li>
    <li>Electrical upgrade services</li>
    <li>Drywall services</li>
    <li>Painting services</li>
  </ul>

  <!-- bathroom left -->
  <div class="abs tab tab-light" style="left:0;top:829px;width:369px;height:31px;">BATHROOM REMODELING</div>
  <div class="abs copy copy-light" style="left:33px;top:872px;width:360px;">When you hire us for your bathroom remodeling<br>project, the possibilities are endless. Our experienced<br>and talented team can:</div>
  <ul class="abs list list-soft list-bullet" style="left:22px;top:925px;">
    <li>Install a custom tile shower</li>
    <li>Build a new vanity</li>
    <li>Install flooring and tile</li>
    <li>Replace your plumbing and light fixtures</li>
  </ul>

  <!-- decks -->
  <div class="abs tab tab-light" style="left:0;top:1011px;width:369px;height:29px;">DECKS/PATIOS</div>
  <div class="abs copy copy-light" style="left:33px;top:1047px;width:370px;">An outdoor space is a great addition to any residential<br>property. When you decide to build a patio or deck,<br>you'll be able to experience a variety of benefits.<br>Your outdoor area will increase your:</div>
  <ul class="abs list list-soft" style="left:33px;top:1112px;">
    <li>Property value</li>
    <li>Curb appeal</li>
    <li>Functional living space</li>
  </ul>

  <!-- right column -->
  <div class="photo photo-room"><div class="fill" role="img" aria-label="Photo of a bright living room with a white sectional sofa and round coffee table"></div></div>

  <div class="abs tab tab-dark" style="left:410px;top:740px;width:274px;height:29px;">HOME ADDITIONS</div>
  <div class="abs copy" style="left:437px;top:775px;width:300px;">No matter what kind of space you need,<br>our team will bring your vision to life.<br>You can hire us if you need a:</div>
  <ul class="abs list list-ink list-bullet" style="left:426px;top:824px;">
    <li>Bathroom addition</li>
    <li>Bedroom addition</li>
    <li>Garage addition</li>
    <li>Basement addition</li>
    <li>Guest room addition</li>
    <li>Living room addition</li>
    <li>Sunroom addition</li>
  </ul>
  <div class="photo photo-lounge" role="img" aria-label="Photo of a light grey sofa against a navy wall with a folding screen and plants"></div>

  <div class="abs tab tab-dark" style="left:410px;top:965px;width:366px;height:30px;">BATHROOM REMODELING</div>
  <div class="abs copy" style="left:437px;top:1002px;width:345px;">When you hire us for your bathroom remodeling<br>project, the possibilities are endless. Our experienced<br>and talented team can:</div>
  <ul class="abs list list-ink list-bullet" style="left:426px;top:1054px;">
    <li>Install a custom tile shower</li>
    <li>Build a new vanity</li>
    <li>Install flooring and tile</li>
    <li>Replace your plumbing and light fixtures</li>
  </ul>

  <div class="abs cta">
    <svg class="abs" style="left:44px;top:22px;" width="28" height="28" viewBox="0 0 24 24" aria-hidden="true">
      <path fill="#fff" d="M6.6 10.8a15.1 15.1 0 0 0 6.6 6.6l2.2-2.2a1 1 0 0 1 1-.25 11.4 11.4 0 0 0 3.6.57 1 1 0 0 1 1 1V20a1 1 0 0 1-1 1A17 17 0 0 1 3 4a1 1 0 0 1 1-1h3.5a1 1 0 0 1 1 1c0 1.250.2 2.450.57 3.570a1 1 0 0 1-.25 1z"/>
    </svg>
    <div class="ask">CALL TODAY FOR YOUR FREE ESTIMATE</div>
    <div class="phone">515-555-0148</div>
    <div class="web">WWW.NORTHBROOKIOWA.COM</div>
  </div>

</div>
</body>
</html>
```